Harborline Auto LLC

Car Dealer Customer Service
Address: 2874 Cresthaven Road, Shelbyville, TN 37162
web: www.harborlineautoxq.net
email: harborlineautoxq@mailnest.example
Phone: (931) 555-0148
Phone: (629) 555-0173

```html
<!DOCTYPE html>
<html lang="en">
<head>
<meta charset="utf-8">
<title>Harborline Auto LLC – Business Card</title>
<link href="https://fonts.googleapis.com/css2?family=Montserrat:wght@700&family=Oswald:wght@600&family=Poppins:wght@400&display=swap" rel="stylesheet">
<style>
  :root{
    --backdrop:#2a2a2b;
    --card:#222326;
    --card-light:#2a2b2f;
    --blue:#1f84c0;
    --gold:#e0a72e;
    --text:#e4e4e4;
    --emboss:#151517;
  }
  *{margin:0;padding:0;box-sizing:border-box}
  html,body{width:1200px;height:1138px;overflow:hidden;background:var(--backdrop)}
  body{position:relative;font-family:"Poppins",sans-serif;color:var(--text)}
  .card{
    position:absolute;left:289px;width:622px;height:374px;border-radius:16px;
    background:linear-gradient(160deg,var(--card) 0%,var(--card-light) 100%);
    overflow:hidden;
  }
  .card--front{top:186px}
  .card--back{top:607px}

  .front-mark{position:absolute;left:0;right:0;top:70px;display:flex;flex-direction:column;align-items:center;gap:18px}
  .front-mark__dot{width:120px;height:120px;border-radius:50%;background:var(--emboss)}
  .front-mark__name{font-family:"Montserrat",sans-serif;font-weight:700;font-size:30px;color:var(--emboss);letter-spacing:.5px;text-transform:uppercase}

  .front-url{position:absolute;left:0;right:0;top:334px;display:flex;align-items:center;justify-content:center;gap:24px;font-size:15px}
  .front-url__rule{width:54px;height:2px;background:var(--gold)}

  .brand{position:absolute;left:0;right:0;top:48px;display:flex;flex-direction:column;align-items:center;gap:14px}
  .brand__dot{width:110px;height:110px;border-radius:50%;background:var(--blue)}
  .brand__name{font-family:"Montserrat",sans-serif;font-weight:700;font-size:31px;color:var(--blue);letter-spacing:.5px;text-transform:uppercase;line-height:1}

  .tagline{position:absolute;left:0;right:0;top:235px;text-align:center;font-size:16px}
  .phone-band{position:absolute;left:0;right:0;top:261px;height:46px;background:var(--blue);display:flex;align-items:center;justify-content:center;gap:22px}
  .phone{display:flex;align-items:center;gap:12px;font-family:"Oswald",sans-serif;font-weight:600;font-size:31px;color:#fff;line-height:1}
  .phone svg{width:28px;height:28px}
  .contact{position:absolute;left:0;right:0;top:313px;text-align:center;font-size:15px;line-height:21px}
</style>
</head>
<body>

<section class="card card--front">
  <div class="front-mark">
    <div class="front-mark__dot"></div>
    <div class="front-mark__name">Harborline Auto</div>
  </div>
  <div class="front-url">
    <span class="front-url__rule"></span>
    <span>www.harborlineautoxq.net</span>
    <span class="front-url__rule"></span>
  </div>
</section>

<section class="card card--back">
  <div class="brand">
    <div class="brand__dot"></div>
    <div class="brand__name">Harborline Auto</div>
  </div>
  <p class="tagline">Car Dealer Customer Service</p>
  <div class="phone-band">
    <div class="phone">
      <svg viewBox="0 0 28 28" aria-hidden="true"><circle cx="14" cy="14" r="12" fill="none" stroke="#e0a72e" stroke-width="2.4"/><path d="M10 8.5c-.8.3-1.6 1.3-1.3 2.8.6 3 3.6 6.4 6.9 7.6 1.4.5 2.4-.2 2.9-1l-2.2-2-1.4.9c-1.3-.6-2.5-1.9-3-3.2l1-1.3z" fill="#e0a72e"/></svg>
      <span>931-555-0148</span>
    </div>
    <div class="phone">
      <svg viewBox="0 0 28 28" aria-hidden="true"><circle cx="14" cy="14" r="12" fill="none" stroke="#e0a72e" stroke-width="2.4"/><path d="M10 8.5c-.8.3-1.6 1.3-1.3 2.8.6 3 3.6 6.4 6.9 7.6 1.4.5 2.4-.2 2.9-1l-2.2-2-1.4.9c-1.3-.6-2.5-1.9-3-3.2l1-1.3z" fill="#e0a72e"/></svg>
      <span>629-555-0173</span>
    </div>
  </div>
  <div class="contact">
    <p>2874 Cresthaven Road, Shelbyville, TN 37162</p>
    <p>www.harborlineautoxq.net &nbsp;|&nbsp; harborlineautoxq@mailnest.example</p>
  </div>
</section>

</body>
</html>
```